CODED website - Breakfree418

I am a successful entrepreneur - have recently sold my business and am semi-retired. I want to give something back, as well as provide a blog for articles and my journeys.

I will also be using this to provide free business and entrepreneurial advice.

I am creating a NOT FOR PROFIT business called Breakfree418.com.au which will provide the following;

1. Blog and articles; my travels, Small to Medium business advice and articles

2. My Bucket List - the 100 things I aim to achieve

3. Free business / start up advice - a section on the website which provides case studies on people / businesses which ask me for advice. We will then chronicle their story and what advice we have given for them to succeed.

My inspiration is the Martin Oxendale idea and website;

http://martinoxendale.example/about-martin/

Obviously I do NOT want a copy of this site, but use this for inspiration.

Furthermore, I would be interested in ongoing collaboration with the successful designer - I will be providing advice and consultancy to start ups, all of which will need web design etc, so there is ongoing referral streams for the successful designer.

I need this to be CODED and then uplifted to the website, so please DO NOT bid on this unless you can provide a coded site and facilitate the upload to BrightHosting.

The NECESSARY tabs / pages

Main landing page - a short introduction into the ethos of Breakfree418

Writing - this will be the blog articles

About

Our Bucket List - a section where we can add our 100 buket list items. Hyperlinked to open a new page which has details on each bucket list item (ie #1 Make Breakfree418 - hyperlink to a new page which then has info on the bucklist item and what we have done)

Breakfree418 - this will be the section where we discuss people / businesses that we are helping. We will have an opening intro section + a link to the contact us page so they can ask us for the free advice. This will be the section where we have case studies into businesses / people that we have helped.

Hey everyone!

I'm really keen to get this website launched and looking amazing - if you have any questions, or would like to discuss anything at all, please email me at

dane@pollwick.example.com.au

As I mentioned in the brief, I am doing this site to give back; I will not be earning a cent, and I will not be trying to earn any funds. I'm doing it simply to help other start ups or entrepreneurs, so I really want this site to look amazing.

I hope someone reads this and is inspired, and wants to be involved in this social enterprise with me.

Really excited to hear from you all and see your designs!

Industry/Entity Type

Business

Requirements
Must have
• MUST BE CODED and uplifted to the BrightHosting registered domain - www.breakfree418.com.au - happy to discuss additional costings for this with successful designer.

Separate pages for each section (as outlined in the brief above)

Blog section to look similar to http://martinoxendale.example/3x5/

Comprehensive website - not a simple wordpress template theme with some minor modifications. I will immediately reject any simple template design. I am looking for a slick, fully functioning website design.

PLEASE BE AWARE that I am looking for ongoing collaboration with the www.breakfree418.com.au.

I am trying this website as I want to find a young, energetic, vibrant, dynamic designer - this is your opportunity to be a part of something big, as this website will be huge!

Please do not submit a design if you are not motivated and ready for something big.

```html
<!DOCTYPE html>
<html lang="en">
<head>
<meta charset="utf-8">
<title>Breakfree418 – Home</title>
<link href="https://fonts.googleapis.com/css2?family=Oswald:wght@400;500&family=PT+Sans:wght@400&display=swap" rel="stylesheet">
<style>
:root{
  --outer:#a38f6a;
  --page:#f6f3ec;
  --red:#d42a2a;
  --ink:#1c1c1c;
  --body:#3a3a3a;
  --cream:#faefd9;
  --cream-line:#d9c9a4;
  --muted:#8a7e6a;
  --dark:#1d2533;
}
*{box-sizing:border-box;margin:0;padding:0}
html,body{width:1200px;height:1200px;overflow:hidden}
body{background:var(--outer);font-family:"PT Sans",sans-serif;color:var(--body);position:relative}
.page{position:absolute;left:200px;top:0;width:800px;height:1200px;background:var(--page);box-shadow:0 0 6px rgba(0,0,0,.25)}
.abs{position:absolute}
.account-links{right:16px;top:6px;font-size:11px;color:var(--red)}
.account-links span{margin:0 8px}
.brand{left:30px;top:38px;display:flex;align-items:center;gap:8px}
.brand-name{font-family:"Oswald",sans-serif;font-weight:500;font-size:22px;letter-spacing:5px;color:var(--ink)}
.brand-mark{width:14px;height:14px;background:var(--red)}
.nav{left:296px;top:40px;display:flex}
.nav a{width:96px;height:40px;display:flex;align-items:center;justify-content:center;text-align:center;font-family:"Oswald",sans-serif;font-size:14px;line-height:16px;color:var(--red);text-decoration:none}
.nav a.active{background:var(--red);color:#fff}
.slider{left:16px;top:96px;width:768px;height:264px;background:var(--dark)}
.slider .scene{position:absolute;left:32px;top:0;width:704px;height:264px;background:linear-gradient(180deg,#2d7fd0 0%,#9fd0f2 55%,#d8ecf6 80%,#8fa5b4 100%)}
.slider .arrow{position:absolute;top:116px;color:#fff;font-size:30px;font-family:"Oswald",sans-serif;line-height:1}
h2{font-family:"Oswald",sans-serif;font-weight:500;font-size:22px;color:var(--ink);line-height:1;text-transform:uppercase}
h2 em{font-style:normal;color:var(--red)}
p{font-size:9.5px;line-height:19.2px}
.photo{background:linear-gradient(135deg,#8a6a3c,#c9a676)}
.welcome-text{left:216px;top:419px;width:296px}
.welcome-more{left:16px;top:551px;width:500px}
.ethos-text{left:544px;top:419px;width:244px}
.video{left:544px;top:488px;width:240px;height:152px;background:linear-gradient(180deg,#3a6fa8,#9ec6e0 55%,#e7e2d6)}
.video .bar{position:absolute;left:0;bottom:0;width:240px;height:18px;background:#1f1f1f}
.video .track{position:absolute;left:14px;top:7px;width:150px;height:4px;background:#555}
.video .track i{display:block;width:95px;height:4px;background:#bbb}
.video .time{position:absolute;right:16px;top:4px;font-size:6px;color:#999}
.video .play{position:absolute;left:96px;top:53px;width:46px;height:28px;background:rgba(0,0,0,.75);border-radius:3px}
.card-text{text-align:center;font-size:9px;line-height:14.4px;width:160px}
.btn{display:flex;align-items:center;justify-content:center;background:var(--red);color:#fff;font-family:"Oswald",sans-serif;font-size:13px}
.bucket{left:544px;top:704px;width:240px;height:192px;background:var(--cream);border:1px solid var(--cream-line);padding:13px 0 0 18px}
.bucket li{list-style:none;font-family:"Oswald",sans-serif;font-size:12.5px;color:var(--muted);height:24px;line-height:24px;display:flex;align-items:center;gap:9px}
.bucket li svg{flex:none}
.carousel{left:16px;top:960px;width:768px;height:160px;background:var(--cream);border:1px solid var(--cream-line)}
.carousel .side{position:absolute;top:0;width:16px;height:158px;background:var(--outer);color:#fff;font-family:"Oswald",sans-serif;font-size:20px;display:flex;align-items:center;justify-content:center}
.travel-card{position:absolute;top:8px;width:128px}
.travel-card .photo{width:128px;height:64px;border:1px solid #aaa}
.travel-card p{font-size:8.5px;line-height:14.4px;text-align:center;margin-top:8px;width:140px;margin-left:-6px}
.travel-card .btn{width:64px;height:24px;margin:10px auto 0;font-size:12px}
.footer-rule{left:16px;top:1152px;width:768px;height:1px;background:#ddd6c8}
.footer-text{left:16px;top:1169px;font-size:9px;color:#6b6257}
.socials{right:16px;top:1168px;display:flex;gap:6px}
.socials span{width:16px;height:16px;background:#d5cdbf;border-radius:2px}
</style>
</head>
<body>
<div class="page">
  <div class="abs account-links">My Account<span>:</span>Login</div>
  <div class="abs brand"><span class="brand-name">BREAKFREE418</span><span class="brand-mark"></span></div>
  <nav class="abs nav">
    <a class="active" href="#">HOME</a><a href="#">ABOUT</a><a href="#">ARTICLES</a><a href="#">BUSINESS<br>ADVICE</a><a href="#">CONTACT</a>
  </nav>

  <div class="abs slider">
    <div class="scene" role="img" aria-label="Hero illustration: an island of city towers floating on a globe, with a ship and an aeroplane in a blue sky"></div>
    <span class="arrow" style="left:8px">❮</span><span class="arrow" style="right:8px">❯</span>
  </div>

  <h2 class="abs" style="left:16px;top:390px">Welcome to <em>Breakfree418</em></h2>
  <div class="abs photo" style="left:16px;top:424px;width:184px;height:104px;border:1px solid #aaa" role="img" aria-label="Couple walking along a wooden path through autumn woods"></div>
  <p class="abs welcome-text">Lorem Ipsum is simply dummy text of the printing and typesetting industry. Lorem Ipsum has been the industry's standard dummy text ever since the 1500s, when an unknown printer took a galley of type and scrambled it to make a type specimen book. It has survived not only five centuries, but also the leap into electronic typesetting, remaining essentially unchanged.</p>
  <p class="abs welcome-more">It was popularised in the 1960s with the release of Setwell sheets containing Lorem Ipsum passages, and more recently with desktop publishing software like Pressline Layout including versions of Lorem Ipsum. t was popularised in the 1960s with the release of Setwell sheets containing Lorem Ipsum passages, and more recently with desktop publishing software like Pressline Layout including versions of Lorem Ipsum.</p>

  <h2 class="abs" style="left:544px;top:390px">Ethos of <em>Breakfree418</em></h2>
  <p class="abs ethos-text">Lorem Ipsum is simply dummy text of the printing and typesetting industry. Lorem Ipsum has been the industry's standard dummy text ever since the 1500s</p>
  <div class="abs video" role="img" aria-label="Video still: hammock between palm trees on a sunny beach">
    <div class="play"><svg width="46" height="28" viewBox="0 0 46 28"><path d="M19 8 L29 14 L19 20 Z" fill="#fff"/></svg></div>
    <div class="bar"><svg style="position:absolute;left:4px;top:5px" width="6" height="8"><path d="M0 0 L6 4 L0 8Z" fill="#bbb"/></svg><div class="track"><i></i></div><span class="time">1:02 / 2:00 &nbsp;HD</span></div>
  </div>

  <h2 class="abs" style="left:16px;top:670px">Business <em>Advice</em></h2>
  <div class="abs photo" style="left:16px;top:704px;width:160px;height:96px;background:linear-gradient(180deg,#2f5a2a,#8fae6a)" role="img" aria-label="Rope bridge through a green forest"></div>
  <div class="abs photo" style="left:184px;top:704px;width:160px;height:96px;background:linear-gradient(180deg,#7b8a4a,#9a6a3a)" role="img" aria-label="Cyclist riding on a leafy forest trail"></div>
  <div class="abs photo" style="left:352px;top:704px;width:160px;height:96px;background:linear-gradient(180deg,#a34a3a,#e6a92a)" role="img" aria-label="Yellow tram on a city street"></div>
  <p class="abs card-text" style="left:16px;top:805px">Lorem Ipsum is simply dummy text of the printing and typesetting industry. Lorem Ipsum has been the industry's standard dummy text 1500s.</p>
  <p class="abs card-text" style="left:184px;top:805px">Lorem Ipsum is simply dummy text of the printing and typesetting industry. Lorem Ipsum has been the industry's standard dummy text 1500s.</p>
  <p class="abs card-text" style="left:352px;top:805px">Lorem Ipsum is simply dummy text of the printing and typesetting industry. Lorem Ipsum has been the industry's standard dummy text 1500s.</p>
  <a class="abs btn" style="left:52px;top:872px;width:88px;height:24px">READ MORE</a>
  <a class="abs btn" style="left:220px;top:872px;width:88px;height:24px">READ MORE</a>
  <a class="abs btn" style="left:388px;top:872px;width:88px;height:24px">READ MORE</a>

  <h2 class="abs" style="left:544px;top:670px">My <em>Bucket List</em></h2>
  <ul class="abs bucket">
    <li><svg width="6" height="9"><path d="M1 1 L5 4.5 L1 8" stroke="#d42a2a" stroke-width="2" fill="none"/></svg>LOREM IPSUM IS SIMPLY DUMMY TEXT</li>
    <li><svg width="6" height="9"><path d="M1 1 L5 4.5 L1 8" stroke="#d42a2a" stroke-width="2" fill="none"/></svg>LOREM IPSUM IS &nbsp;DUMMY TEXT</li>
    <li><svg width="6" height="9"><path d="M1 1 L5 4.5 L1 8" stroke="#d42a2a" stroke-width="2" fill="none"/></svg>IPSUM IS SIMPLY DUMMY TEXT</li>
    <li><svg width="6" height="9"><path d="M1 1 L5 4.5 L1 8" stroke="#d42a2a" stroke-width="2" fill="none"/></svg>LOREM IPSUM IS SIMPLY TEXT</li>
    <li><svg width="6" height="9"><path d="M1 1 L5 4.5 L1 8" stroke="#d42a2a" stroke-width="2" fill="none"/></svg>LOREM &nbsp;DUMMY TEXT</li>
    <li><svg width="6" height="9"><path d="M1 1 L5 4.5 L1 8" stroke="#d42a2a" stroke-width="2" fill="none"/></svg>IS SIMPLY DUMMY TEXT</li>
    <li><svg width="6" height="9"><path d="M1 1 L5 4.5 L1 8" stroke="#d42a2a" stroke-width="2" fill="none"/></svg>LOREM IPSUM IS SIMPLY DUMMY</li>
  </ul>

  <h2 class="abs" style="left:16px;top:926px">My Travel <em>Articles</em></h2>
  <div class="abs carousel">
    <div class="side" style="left:0">❮</div>
    <div class="side" style="right:0">❯</div>
    <div class="travel-card" style="left:23px"><div class="photo" style="background:linear-gradient(180deg,#7d8a96,#c9ccc6)" role="img" aria-label="Race car on a motor racing track"></div><p>Lorem Ipsum is simply dummy text of the printing and type typesetting industry.</p><div class="btn">MORE</div></div>
    <div class="travel-card" style="left:171px"><div class="photo" style="background:linear-gradient(180deg,#2e4a20,#6f9a3e)" role="img" aria-label="Lush jungle ferns"></div><p>Lorem Ipsum is simply dummy text of the printing and type typesetting industry.</p><div class="btn">MORE</div></div>
    <div class="travel-card" style="left:319px"><div class="photo" style="background:linear-gradient(180deg,#a9c4d8,#d9d3c2)" role="img" aria-label="City buildings under a pale sky"></div><p>Lorem Ipsum is simply dummy text of the printing and type typesetting industry.</p><div class="btn">MORE</div></div>
    <div class="travel-card" style="left:467px"><div class="photo" style="background:linear-gradient(180deg,#8aa6c2,#b99a6a)" role="img" aria-label="Seaside villa terrace with palm trees"></div><p>Lorem Ipsum is simply dummy text of the printing and type typesetting industry.</p><div class="btn">MORE</div></div>
    <div class="travel-card" style="left:615px"><div class="photo" style="background:linear-gradient(180deg,#d9431e,#f2a23a 60%,#c9a0b0)" role="img" aria-label="Skier jumping against a sunset sky"></div><p>Lorem Ipsum is simply dummy text of the printing and type typesetting industry.</p><div class="btn">MORE</div></div>
  </div>

  <div class="abs footer-rule"></div>
  <div class="abs footer-text">Breakfree418 © Copyright 2007 - 2012. All rights reserved. Privacy Policy.</div>
  <div class="abs socials" aria-label="Social links"><span></span><span></span><span></span></div>
</div>
</body>
</html>
```